VOR Exterior Coatings

double sided. the front i want the name of the business each word on a new line with the VOR being bigger. id like teal, black and white colors. the back i want my contact info. Flat, no gloss. Something professional and I want to feel the letters bump put of the card. if possible maybe a paint sprayer in corner. not a car paint spray. (no tank on top of gun)
no vehicle paint sprayers. that means no tank on top of the gun. doesn't have to have a sprayer. black/dark background on the front. white back ground on back with info

```html
<!DOCTYPE html>
<html lang="en">
<head>
<meta charset="utf-8">
<title>VOR Exterior Coatings — Business Card</title>
<link href="https://fonts.googleapis.com/css2?family=Lato:wght@400;700;900&display=swap" rel="stylesheet">
<style>
  :root {
    --teal: #00827f;
    --teal-deep: #00676a;
    --teal-light: #009a96;
    --ink: #111111;
    --grey-text: #5c5c5c;
    --card-white: #f7f7f7;
    --backdrop: #e4e4e4;
  }
  * { margin: 0; padding: 0; box-sizing: border-box; }
  html, body { width: 1200px; height: 1200px; overflow: hidden; }
  body {
    background: var(--backdrop);
    font-family: 'Lato', sans-serif;
    position: relative;
  }
  .card {
    position: absolute;
    left: 262px;
    width: 686px;
    height: 392px;
    border-radius: 22px;
    overflow: hidden;
  }
  .card--details { top: 165px; background: var(--card-white); }
  .card--brand {
    top: 653px;
    background: linear-gradient(35deg, var(--teal-deep) 0%, var(--teal) 55%, var(--teal-light) 100%);
  }

  /* Wordmark */
  .wordmark { position: absolute; font-family: 'Lato', sans-serif; font-weight: 900; text-transform: uppercase; }
  .wordmark__main { display: block; line-height: 1; letter-spacing: -2px; }
  .wordmark__sub { display: block; line-height: 1; letter-spacing: 0.2px; }

  .card--details .wordmark { left: 80px; top: 128px; width: 232px; color: var(--teal); text-align: center; }
  .card--details .wordmark__main { font-size: 122px; }
  .card--details .wordmark__sub { font-size: 23px; margin-top: 2px; }

  .card--brand .wordmark { left: 0; right: 0; top: 108px; color: #ffffff; text-align: center; }
  .card--brand .wordmark__main { font-size: 156px; letter-spacing: -3px; }
  .card--brand .wordmark__sub { font-size: 30px; margin-top: 0; }

  .divider {
    position: absolute;
    left: 341px; top: 92px;
    width: 1px; height: 208px;
    background: #6a6a6a;
  }

  .contact { position: absolute; left: 365px; top: 94px; color: var(--grey-text); }
  .contact__name { font-size: 24px; font-weight: 700; color: var(--teal); letter-spacing: 0.3px; line-height: 1.1; }
  .contact__role { font-size: 16px; line-height: 1.2; margin-bottom: 10px; }
  .contact__address { font-size: 17px; line-height: 1.18; margin-bottom: 9px; }
  .contact__list { list-style: none; }
  .contact__item { display: flex; align-items: center; font-size: 17px; line-height: 20px; }
  .contact__icon { width: 16px; height: 16px; margin-right: 10px; fill: var(--teal); flex: none; }
</style>
</head>
<body>

<section class="card card--details" aria-label="Card front with contact details">
  <div class="wordmark">
    <span class="wordmark__main">VOR</span>
    <span class="wordmark__sub">Exterior Coatings</span>
  </div>
  <div class="divider"></div>
  <div class="contact">
    <p class="contact__name">DANIEL MORENO</p>
    <p class="contact__role">Founder &amp; CEO</p>
    <p class="contact__address">4120 Birchwood Court<br>Fairbanks, Alaska 99712</p>
    <ul class="contact__list">
      <li class="contact__item">
        <svg class="contact__icon" viewBox="0 0 24 24"><path d="M6.6 10.8a15.1 15.1 0 0 0 6.6 6.6l2.2-2.2c.3-.3.7-.4 1-.2 1.1.4 2.3.6 3.6.6.6 0 1 .4 1 1V20c0 .6-.4 1-1 1A17 17 0 0 1 3 4c0-.6.4-1 1-1h3.5c.6 0 1 .4 1 1 0 1.3.2 2.5.6 3.6.1.3 0 .7-.2 1z"/></svg>
        555-214-7730
      </li>
      <li class="contact__item">
        <svg class="contact__icon" viewBox="0 0 24 24"><path d="M7 1h10a2 2 0 0 1 2 2v18a2 2 0 0 1-2 2H7a2 2 0 0 1-2-2V3a2 2 0 0 1 2-2zm0 3v14h10V4zm5 15.2a1.2 1.2 0 1 0 0 2.4 1.2 1.2 0 0 0 0-2.4z"/></svg>
        555-308-4162
      </li>
      <li class="contact__item">
        <svg class="contact__icon" viewBox="0 0 24 24"><path d="M6 2h10l2 2v5H6zM3 10h18a2 2 0 0 1 2 2v7H1v-7a2 2 0 0 1 2-2zm3 6v6h12v-6z"/></svg>
        555-671-2085
      </li>
      <li class="contact__item">
        <svg class="contact__icon" viewBox="0 0 24 24"><path d="M2 5h20v14H2zm2 2v.5l8 5 8-5V7zm0 2.8V17h16V9.8l-8 5z"/></svg>
        info@vorexteriorcoatings.com
      </li>
      <li class="contact__item">
        <svg class="contact__icon" viewBox="0 0 24 24"><circle cx="12" cy="12" r="10"/><path d="M8 6c2 1 1 3 3 3s1 3-1 3-2 2-1 4M15 5c-1 2 1 3 2 3s2 2 1 3-3 0-3 3 2 3 2 3" stroke="#f7f7f7" stroke-width="1.6" fill="none"/></svg>
        www.vorexteriorcoatings.com
      </li>
    </ul>
  </div>
</section>

<section class="card card--brand" aria-label="Card back with brand name">
  <div class="wordmark">
    <span class="wordmark__main">VOR</span>
    <span class="wordmark__sub">Exterior Coatings</span>
  </div>
</section>

</body>
</html>
```